Verodex business card

Business card for sustainable investment company called "Verodex". Verodex is an exchange platform selling carbon credits between buyers and sellers. Carbon Credits are an environmental commodity for reducing global carbon emissions.

the card should obviously have our logo and the theme should be sustainability/environment mixed with a trading platform.

Contact Information for Business Card

Logo, Name, Title, Phone, Email

Colors
0054AA
0677BA
7BADD7
CADEEF
E8F1F8
0094D4
00A9DD
6FCCEA
C7EBF8
E9F6FB
00AB8E
00BBA5
67D7C9
C6EFE9
E9F9F6
59FF00
82FF00
B8FF75
E3FFCB
F4FFEA

```html
<!DOCTYPE html>
<html lang="en">
<head>
<meta charset="utf-8">
<title>Verodex business card</title>
<link rel="stylesheet" href="https://fonts.googleapis.com/css2?family=Inter:wght@400;500;600;700&display=swap">
<style>
  :root {
    --stage: #959595;
    --navy: #0b2a55;
    --navy-light: #12366a;
    --navy-deep: #08224a;
    --paper: #ebebeb;
    --paper-light: #f3f3f3;
    --paper-shade: #dcdcdc;
    --ink: #0f2a4f;
    --muted: #8a8a8a;
    --contact: #777777;
    --cyan: #2ad4f0;
    --blue: #1e86f5;
    --white: #ffffff;
  }
  * { margin: 0; padding: 0; box-sizing: border-box; }
  html, body {
    width: 1200px; height: 1000px; overflow: hidden;
    background: var(--stage);
    font-family: "Inter", Arial, sans-serif;
  }
  .stage { position: relative; width: 1200px; height: 1000px; }
  .card {
    position: absolute; top: 191px;
    width: 351px; height: 615px;
    border-radius: 30px; overflow: hidden;
  }
  .card-front { left: 214px; background: var(--navy); }
  .card-back { left: 633px; background: var(--paper); text-align: center; }

  .front-pattern {
    position: absolute; inset: 0;
    background:
      radial-gradient(ellipse 70% 45% at 50% 30%, rgba(40, 80, 140, 0.35), rgba(40, 80, 140, 0) 70%),
      repeating-linear-gradient(180deg, var(--navy-light) 0 22px, var(--navy) 22px 58px),
      var(--navy);
    opacity: 0.95;
  }
  .front-pattern::after {
    content: ""; position: absolute; inset: 0;
    background: linear-gradient(180deg, rgba(8, 34, 74, 0) 60%, var(--navy-deep) 100%);
  }
  .front-brand {
    position: absolute; left: 114px; top: 511px;
    display: flex; align-items: center; gap: 12px;
  }
  .brand-dot {
    width: 44px; height: 44px; border-radius: 50%;
    background: var(--blue);
  }
  .front-brand .brand-name {
    color: var(--white); font-weight: 600; font-size: 28px; letter-spacing: 0.6px;
  }

  .back-watermark {
    position: absolute; left: 0; right: 0; bottom: 0; height: 250px;
    background:
      radial-gradient(ellipse 75% 85% at 55% 85%, var(--paper-light) 0%, var(--paper-shade) 55%, rgba(235, 235, 235, 0) 80%);
  }
  .back-brand { position: absolute; left: 0; right: 0; top: 54px; }
  .back-brand .brand-dot { width: 38px; height: 38px; margin: 0 auto 10px; }
  .back-brand .brand-name {
    color: var(--ink); font-weight: 700; font-size: 28px; letter-spacing: 0.3px;
  }
  .person { position: absolute; left: 0; right: 0; top: 171px; }
  .person-name { color: var(--ink); font-weight: 700; font-size: 21px; letter-spacing: 0.7px; line-height: 26px; }
  .person-title { color: var(--muted); font-size: 18px; letter-spacing: 0.8px; line-height: 22px; }

  .contact-icons {
    position: absolute; left: 0; right: 0; top: 252px;
    display: flex; justify-content: center; gap: 7px;
  }
  .contact-icon {
    width: 33px; height: 33px; border-radius: 50%;
    background: linear-gradient(135deg, var(--cyan), var(--blue));
    display: flex; align-items: center; justify-content: center;
  }
  .contact-list {
    position: absolute; left: 0; right: 0; top: 293px;
    list-style: none; color: var(--contact);
    font-size: 16px; letter-spacing: 0.8px; line-height: 23px;
  }
</style>
</head>
<body>
<main class="stage">
  <section class="card card-front">
    <div class="front-pattern" role="img" aria-label="Embossed repeating brand pattern on navy"></div>
    <div class="front-brand">
      <span class="brand-dot"></span>
      <span class="brand-name">VERODEX</span>
    </div>
  </section>

  <section class="card card-back">
    <div class="back-watermark" role="img" aria-label="Large faint embossed brand watermark"></div>
    <div class="back-brand">
      <div class="brand-dot"></div>
      <div class="brand-name">VERODEX</div>
    </div>
    <div class="person">
      <div class="person-name">Name Surname</div>
      <div class="person-title">Title</div>
    </div>
    <div class="contact-icons">
      <span class="contact-icon">
        <svg width="15" height="15" viewBox="0 0 24 24" fill="#fff"><path d="M6.6 10.8a15.1 15.1 0 0 0 6.6 6.6l2.2-2.2c.3-.3.7-.4 1-.2 1.1.4 2.3.6 3.6.6.6 0 1 .4 1 1V20c0 .6-.4 1-1 1C10.6 21 3 13.4 3 4c0-.6.4-1 1-1h3.5c.6 0 1 .4 1 1 0 1.3.2 2.5.6 3.6.1.3 0 .7-.2 1z"/></svg>
      </span>
      <span class="contact-icon">
        <svg width="16" height="16" viewBox="0 0 24 24" fill="#fff"><path d="M3 6h18v12H3z"/><path d="M3 6l9 7 9-7" fill="none" stroke="#1e86f5" stroke-width="1.5"/></svg>
      </span>
      <span class="contact-icon">
        <svg width="16" height="16" viewBox="0 0 24 24" fill="none" stroke="#fff" stroke-width="1.6"><circle cx="12" cy="12" r="9"/><ellipse cx="12" cy="12" rx="4" ry="9"/><path d="M3 12h18M5 7h14M5 17h14"/></svg>
      </span>
    </div>
    <ul class="contact-list">
      <li>012•345•6789</li>
      <li>name@website.com</li>
      <li>website.com</li>
    </ul>
  </section>
</main>
</body>
</html>
```